University Student Business Card

Looking for a professional university student business card. Student is studying business with a focus on marketing. Some combination using a monogram and/or full name on the front with full name, university details and contact information on the back. Card should be modern design for a young professional. Prefer use of royal blue, black and white but am open to other uses of colour palette if it reinforces young/trendy style. Initials for a monogram are: KR. Full details will be provided in private consultation with designer(s).

Target Market(s)

Professional business people, marketers, advertisers, consultants

Industry/Entity Type

Business, marketing

Contact Information for Business Card

Monogram or personal logo, full name, university name, program of study, phone number, email address, pathfolio address

Other font styles liked:
• Open to suggestion to fulfill above requirements

Colors
0054AA
0677BA
7BADD7
CADEEF
E8F1F8

Requirements
Must have
• Monogram using letters K and R, and incorporate the business card details listed in the brief (specific details including personal contact info will be shared with successful designer to ensure privacy)
Nice to have
• Personal brand using monogram or personal logo (not a business logo)

```html
<!DOCTYPE html>
<html lang="en">
<head>
<meta charset="UTF-8">
<title>Kieran Rowe — Student Business Card</title>
<link rel="stylesheet" href="https://fonts.googleapis.com/css2?family=Bebas+Neue&family=Lato:wght@400;700&display=swap">
<style>
  :root {
    --royal: #0054aa;
    --royal-deep: #004f9f;
    --ink: #2b2b2b;
    --white: #ffffff;
    --paper: #fbfbfb;
    --rule-light: #7badd7;
    --rule-grey: #9a9a9a;
    --stage: #2a2a2a;
  }
  * { box-sizing: border-box; margin: 0; padding: 0; }
  html, body {
    width: 1200px;
    height: 1108px;
    overflow: hidden;
    background: var(--stage);
  }
  .sheet {
    width: 1200px;
    height: 1108px;
    display: flex;
    align-items: center;
    justify-content: center;
    gap: 64px;
  }
  .card {
    width: 440px;
    height: 760px;
    border-radius: 26px;
    display: flex;
    flex-direction: column;
    align-items: center;
  }

  /* Back: university details */
  .card--back {
    background: var(--royal);
    color: var(--white);
    padding-top: 210px;
  }
  .university-name {
    font-family: "Bebas Neue", "Oswald", sans-serif;
    font-weight: 400;
    font-size: 100px;
    line-height: 0.86;
    text-align: center;
    letter-spacing: 0.5px;
  }
  .divider {
    width: 210px;
    height: 1px;
    background: var(--rule-light);
    margin: 22px 0 16px;
  }
  .address {
    font-family: "Lato", sans-serif;
    font-size: 21px;
    line-height: 1.3;
    text-align: center;
  }
  .icon-row {
    display: flex;
    align-items: center;
    gap: 8px;
    margin: 24px 0 20px;
  }
  .icon-row__rule {
    width: 58px;
    height: 1px;
    background: var(--rule-light);
    margin: 0 10px;
  }
  .icon-tile {
    width: 30px;
    height: 30px;
    background: var(--white);
    border-radius: 5px;
    display: flex;
    align-items: center;
    justify-content: center;
  }
  .contact-list {
    list-style: none;
    font-family: "Lato", sans-serif;
    font-size: 21px;
    line-height: 1.4;
    text-align: center;
  }

  /* Front: monogram and name */
  .card--front {
    background: var(--paper);
    padding-top: 220px;
  }
  .monogram {
    font-family: "Bebas Neue", "Oswald", sans-serif;
    font-size: 230px;
    line-height: 0.9;
    color: var(--royal);
    letter-spacing: 4px;
  }
  .person-name {
    font-family: "Bebas Neue", "Oswald", sans-serif;
    font-size: 58px;
    line-height: 1;
    color: var(--royal);
    margin-top: 60px;
    letter-spacing: 0.5px;
  }
  .person-role {
    font-family: "Lato", sans-serif;
    font-size: 22px;
    color: var(--ink);
    margin-top: 2px;
  }
  .divider--grey {
    width: 90px;
    background: var(--rule-grey);
    margin: 16px 0 14px;
  }
  .profile-link {
    display: flex;
    align-items: center;
    gap: 12px;
    font-family: "Lato", sans-serif;
    font-size: 21px;
    color: var(--ink);
  }
  .profile-link__dot {
    width: 26px;
    height: 26px;
    border-radius: 50%;
    background: var(--royal);
  }
</style>
</head>
<body>
<main class="sheet">
  <section class="card card--back" aria-label="Card back">
    <h1 class="university-name">University<br>Name</h1>
    <div class="divider"></div>
    <p class="address">421, Address line here<br>45452, Country Name</p>
    <div class="icon-row">
      <span class="icon-row__rule"></span>
      <span class="icon-tile" aria-label="Phone">
        <svg width="20" height="20" viewBox="0 0 20 20"><path d="M2 7c0-3 16-3 16 0l-3 1-1-2H6L5 8z M5 9h10l2 7H3z" fill="#0054aa"/><circle cx="10" cy="12.5" r="2" fill="#fff"/></svg>
      </span>
      <span class="icon-tile" aria-label="Email">
        <svg width="20" height="20" viewBox="0 0 20 20"><rect x="2" y="4" width="16" height="12" fill="none" stroke="#0054aa" stroke-width="2"/><path d="M2 4l8 7 8-7" fill="none" stroke="#0054aa" stroke-width="2"/></svg>
      </span>
      <span class="icon-tile" aria-label="Website">
        <svg width="20" height="20" viewBox="0 0 20 20"><circle cx="10" cy="10" r="7.5" fill="none" stroke="#0054aa" stroke-width="2"/><path d="M2.5 10h15M10 2.5c-4 4-4 11 0 15M10 2.5c4 4 4 11 0 15" fill="none" stroke="#0054aa" stroke-width="1.4"/></svg>
      </span>
      <span class="icon-row__rule"></span>
    </div>
    <ul class="contact-list">
      <li>055-318 402 761</li>
      <li>hello@kieranrowe.com</li>
      <li>www.kieranrowe.com</li>
    </ul>
  </section>

  <section class="card card--front" aria-label="Card front">
    <div class="monogram">KR</div>
    <h2 class="person-name">Kieran Rowe</h2>
    <p class="person-role">Business Marketing</p>
    <div class="divider divider--grey"></div>
    <p class="profile-link"><span class="profile-link__dot"></span>pathfolio.com/name</p>
  </section>
</main>
</body>
</html>
```